Business Card Design Project

Beam Clinic Hub

Dr Lomen Priscu M.D, F.R.C.S
Vascular and Vein Surgery

47-15 Quillford Avenue, Suite 318
Astoria
NY 11103

212-555-0183
718-555-0146
www.mendorapro.us back of the card for scheduled appointments up to 5 appointment dates

Target Market(s)

Male and Female patients from 25 onwards with spider veins or varicose veins

Industry/Entity Type

Business

Font styles to use
Serif

Colors
86cae6
85abd2
0456a4

Requirements
Must have
• Modern Sophisticated design using light blue and grey text
Should not have
• hearts or flowers

```html
<!DOCTYPE html>
<html lang="en">
<head>
<meta charset="utf-8">
<title>Beam Clinic Hub – Business Card</title>
<link rel="stylesheet" href="https://fonts.googleapis.com/css2?family=EB+Garamond:wght@400;500;600&display=swap">
<style>
  :root {
    --brand-blue: #0456a4;
    --mid-blue: #85abd2;
    --light-blue: #86cae6;
    --text-grey: #4a4a4a;
    --rule-grey: #c8c8c8;
    --panel-border: #6b7480;
    --page-bg: #e9ecef;
    --card-white: #ffffff;
  }
  * { box-sizing: border-box; margin: 0; padding: 0; }
  html, body {
    width: 1200px; height: 845px; overflow: hidden;
    background: var(--page-bg);
    font-family: "EB Garamond", serif;
  }
  .canvas {
    width: 1200px; height: 845px;
    display: flex; flex-direction: column; align-items: center; justify-content: center;
    gap: 25px;
  }
  .card {
    position: relative;
    width: 700px; height: 400px;
    box-shadow: 0 4px 14px rgba(0,0,0,0.15);
    overflow: hidden;
  }

  /* Front */
  .card-front { background: var(--card-white); color: var(--text-grey); }
  .brand {
    position: absolute; top: 78px; left: 0; right: 0;
    display: flex; align-items: center; justify-content: center; gap: 16px;
  }
  .brand-name {
    font-size: 52px; font-weight: 500; color: var(--brand-blue); letter-spacing: 1px;
  }
  .brand-dot {
    width: 18px; height: 18px; border-radius: 50%; background: var(--light-blue);
  }
  .doctor {
    position: absolute; left: 42px; top: 212px; right: 42px;
  }
  .doctor-name { font-size: 22px; color: var(--brand-blue); }
  .doctor-role {
    display: flex; align-items: center; gap: 10px;
    font-size: 15px; margin-top: 2px;
  }
  .doctor-role::after {
    content: ""; flex: 1; height: 1px; background: var(--rule-grey);
  }
  .contacts {
    position: absolute; left: 42px; top: 292px;
    list-style: none; font-size: 15px; line-height: 25px;
  }
  .contacts li { display: flex; align-items: center; gap: 6px; }
  .contacts svg { width: 15px; height: 15px; }
  .address {
    position: absolute; left: 440px; top: 300px;
    font-size: 15px; line-height: 25px; font-style: normal;
  }
  .front-band {
    position: absolute; left: 0; right: 0; bottom: 0; height: 20px;
    background: var(--brand-blue);
  }

  /* Back */
  .card-back { background: var(--brand-blue); color: var(--card-white); }
  .appointments-title {
    position: absolute; top: 26px; left: 0; right: 0;
    text-align: center; font-size: 15px; letter-spacing: 1px;
  }
  .appointments-panel {
    position: absolute; left: 50px; top: 56px; width: 600px; height: 250px;
    background: var(--card-white);
    border: 3px solid var(--panel-border); border-radius: 12px;
    padding: 22px 40px 0;
    color: var(--text-grey);
  }
  .slot {
    display: flex; align-items: flex-end; gap: 8px;
    font-size: 12px; height: 38px;
  }
  .slot .field { display: flex; align-items: flex-end; gap: 4px; }
  .slot .date-field { flex: 1.4; }
  .slot .time-field { flex: 1; }
  .slot .line { flex: 1; border-bottom: 1px dotted #9aa0a6; height: 1px; margin-bottom: 3px; }
  .hours {
    position: absolute; left: 55px; top: 328px;
    font-size: 14px; line-height: 20px;
  }
</style>
</head>
<body>
<main class="canvas">

  <section class="card card-front" aria-label="Card front">
    <div class="brand">
      <span class="brand-name">Beam Clinic Hub</span>
      <span class="brand-dot"></span>
    </div>

    <div class="doctor">
      <p class="doctor-name">Dr Lomen Priscu M.D, F.R.C.S</p>
      <p class="doctor-role">Vascular and Vein Surgery</p>
    </div>

    <ul class="contacts">
      <li>
        <svg viewBox="0 0 16 16" aria-hidden="true"><circle cx="8" cy="8" r="8" fill="var(--brand-blue)"/><path d="M4.5 5.5c0-1 .8-1.2 1.3-1.2l1 1.8-.8.8c.4 1 1.2 1.8 2.2 2.2l.8-.8 1.8 1c0 .5-.2 1.3-1.2 1.3-3 0-5.1-2.1-5.1-5.1z" fill="#fff"/></svg>
        212-555-0183
      </li>
      <li>
        <svg viewBox="0 0 16 16" aria-hidden="true"><circle cx="8" cy="8" r="8" fill="var(--brand-blue)"/><rect x="5.5" y="3.5" width="5" height="9" rx="1" fill="none" stroke="#fff" stroke-width="1.2"/><circle cx="8" cy="11" r=".6" fill="#fff"/></svg>
        718-555-0146
      </li>
      <li>
        <svg viewBox="0 0 16 16" aria-hidden="true"><circle cx="8" cy="8" r="8" fill="var(--brand-blue)"/><g fill="none" stroke="#fff" stroke-width=".9"><circle cx="8" cy="8" r="4.5"/><ellipse cx="8" cy="8" rx="2" ry="4.5"/><path d="M3.5 8h9"/></g></svg>
        www.mendorapro.us
      </li>
    </ul>

    <address class="address">
      47-15 Quillford Avenue<br>
      Suite 318, Astoria<br>
      NY 11103
    </address>

    <div class="front-band"></div>
  </section>

  <section class="card card-back" aria-label="Card back">
    <h2 class="appointments-title">APPOINTMENTS</h2>
    <div class="appointments-panel">
      <div class="slot"><span class="field date-field">Date<span class="line"></span></span><span class="field time-field">Time<span class="line"></span></span></div>
      <div class="slot"><span class="field date-field">Date<span class="line"></span></span><span class="field time-field">Time<span class="line"></span></span></div>
      <div class="slot"><span class="field date-field">Date<span class="line"></span></span><span class="field time-field">Time<span class="line"></span></span></div>
      <div class="slot"><span class="field date-field">Date<span class="line"></span></span><span class="field time-field">Time<span class="line"></span></span></div>
      <div class="slot"><span class="field date-field">Date<span class="line"></span></span><span class="field time-field">Time<span class="line"></span></span></div>
    </div>
    <div class="hours">
      <p>Hours</p>
      <p>Monday to Saturday - 9:00am to 5:00pm</p>
    </div>
  </section>

</main>
</body>
</html>
```